Bespoke Branding Agency "Tidal Crest" seeks uplifting wordpress site

Looking for a SIMPLE, CLEAN, easy to manage wordpress site for our start-up Branding business. Our company is "Tidal Crest" and the site should reflect our vision.

We formed the company after making the decision never to work the average 9 to 5 work life again. We have vowed to never work in traditional corporate culture again. We are committed to a happier life with reduced stress and increased job satisfaction.

We want to build brands that make people happy.

We want to work with people who believe that you don’t have to be an asshole to be successful.

We believe that success should not be measured in monetary terms, but rather in happiness scores.

We believe in the Corwin Ashdale song lyric "Rivers bend toward evening”.

We love sunflowers.

We prefer brevity over long wind.

We are motivated by creativity not money.

We love spending time with friends and family, and see this as our main priority in life.

We know life is short.

```html
<!DOCTYPE html>
<html lang="en">
<head>
<meta charset="utf-8">
<title>Tidal Crest — Portfolio</title>
<link rel="stylesheet" href="https://fonts.googleapis.com/css2?family=Source+Sans+3:wght@300;400&display=swap">
<style>
  :root {
    --sunflower: #fbb11b;
    --white: #ffffff;
    --paper: #f4f4f4;
    --mist: #e9e9e9;
    --ink: #0d0d0d;
    --night: #1d2530;
    --sky: #4aa3f0;
  }
  * { margin: 0; padding: 0; box-sizing: border-box; }
  html, body {
    width: 1200px;
    height: 900px;
    overflow: hidden;
    background: var(--sunflower);
  }
  .portfolio-section {
    position: relative;
    width: 1200px;
    height: 900px;
    overflow: hidden;
    background: var(--sunflower);
    border-top: 3px solid var(--white);
    font-family: "Source Sans 3", "Helvetica Neue", Arial, sans-serif;
  }
  .section-notch {
    position: absolute;
    top: -3px;
    left: 530px;
    width: 136px;
    height: 62px;
  }
  .section-title {
    position: absolute;
    top: 84px;
    left: 0;
    width: 1200px;
    text-align: center;
    color: var(--white);
    font-weight: 300;
    font-size: 98px;
    line-height: 1;
    letter-spacing: -1px;
  }
  .portfolio-grid {
    position: absolute;
    top: 300px;
    left: 78px;
    width: 1038px;
    height: 600px;
    overflow: hidden;
  }
  .work-tile {
    position: absolute;
    overflow: hidden;
  }
  .tile-flower {
    left: 0; top: 0; width: 259px; height: 300px;
    background: radial-gradient(circle at 50% 50%, #fde7d8 0%, #f6f1fa 45%, var(--white) 75%);
  }
  .tile-divider {
    left: 0; top: 300px; width: 259px; height: 37px;
    background: var(--mist);
  }
  .tile-swoosh {
    left: 0; top: 337px; width: 259px; height: 263px;
    background: linear-gradient(160deg, #0a0a0a 0%, #1a1a1a 50%, #5a1a1a 80%, #b21c1c 100%);
  }
  .tile-swirl {
    left: 259px; top: 0; width: 260px; height: 475px;
    background: radial-gradient(circle at 45% 55%, #d8c2e6 0%, #f4d9e2 30%, #fbfbfb 65%);
  }
  .tile-mark-m {
    left: 259px; top: 475px; width: 260px; height: 125px;
    background: linear-gradient(180deg, #f0f0f0 0%, #e2ecef 100%);
  }
  .tile-ribbon {
    left: 519px; top: 0; width: 260px; height: 300px;
    background: linear-gradient(135deg, #f4e61c 0%, #8cc63f 40%, #2ea6dc 70%, #8e2e8f 100%);
  }
  .tile-lumo {
    left: 519px; top: 300px; width: 260px; height: 300px;
    background: linear-gradient(180deg, #26303d 0%, var(--night) 100%);
    display: flex;
    flex-direction: column;
    align-items: center;
    justify-content: flex-end;
    padding-bottom: 8px;
  }
  .lumo-name {
    color: var(--sky);
    font-weight: 400;
    font-size: 92px;
    line-height: 1;
    margin-bottom: 22px;
  }
  .lumo-tagline {
    color: var(--sky);
    font-weight: 400;
    font-size: 30px;
    letter-spacing: 3px;
    line-height: 1;
  }
  .tile-sphere {
    left: 779px; top: 0; width: 259px; height: 475px;
    background: radial-gradient(circle at 45% 42%, #f5a623 0%, #e06a1a 30%, #f6d5b8 55%, var(--paper) 70%);
  }
  .tile-ring {
    left: 779px; top: 475px; width: 259px; height: 125px;
    background: radial-gradient(circle at 55% 110%, #c9c9c9 0%, #e6e6e6 55%, var(--paper) 80%);
  }
</style>
</head>
<body>
  <section class="portfolio-section">
    <svg class="section-notch" viewBox="0 0 136 62" aria-hidden="true">
      <polygon points="0,0 136,0 68,62" fill="#ffffff"/>
    </svg>

    <h1 class="section-title">PORTFOLIO</h1>

    <div class="portfolio-grid">
      <div class="work-tile tile-flower" role="img" aria-label="Logo artwork: multicoloured swirling flower of figures"></div>
      <div class="work-tile tile-divider"></div>
      <div class="work-tile tile-swoosh" role="img" aria-label="Logo artwork: silver and red swoosh on black"></div>

      <div class="work-tile tile-swirl" role="img" aria-label="Logo artwork: rainbow ribbon swirl on white"></div>
      <div class="work-tile tile-mark-m" role="img" aria-label="Logo artwork: colourful faceted letter mark"></div>

      <div class="work-tile tile-ribbon" role="img" aria-label="Logo artwork: colour-blocked ribbon shape"></div>
      <div class="work-tile tile-lumo">
        <span class="lumo-name">Lumo</span>
        <span class="lumo-tagline">Stay Bright</span>
      </div>

      <div class="work-tile tile-sphere" role="img" aria-label="Logo artwork: glowing orange sphere with red dot pattern"></div>
      <div class="work-tile tile-ring" role="img" aria-label="Logo artwork: grey ring mark with red centre"></div>
    </div>
  </section>
</body>
</html>
```